Business Card Design

Business Card for professional consulting firm working with large financial institutions.

Target Market(s)

Executive buyers

Industry/Entity Type

Banking

Contact Information for Business Card

Mild creativity wanted. Not boring, but do elaborate artwork.

Font styles to use
Serif
Sans Serif

Colors

Designer to choose colors to be used in the design.

Requirements
Must have
• Standard business card features - company name, individual name, telephone, website, email, locations.
Nice to have
• Two colors
Should not have
• too many colors, fancy printing, cartoons.

```html
<!DOCTYPE html>
<html lang="en">
<head>
<meta charset="utf-8">
<title>Meridian Axis – Business Card</title>
<link rel="stylesheet" href="https://fonts.googleapis.com/css2?family=Lato:wght@400;700&display=swap">
<style>
  :root {
    --navy: #0a2c86;
    --navy-deep: #08257a;
    --navy-light: #0d3597;
    --paper: #f5f5f5;
    --silver: #c9c9c9;
    --grey-text: #6d6d6d;
    --white: #ffffff;
    --backdrop: #3a3a3c;
  }
  * { margin: 0; padding: 0; box-sizing: border-box; }
  html, body { width: 1200px; height: 782px; overflow: hidden; }
  body {
    background: var(--backdrop);
    font-family: "Lato", Arial, sans-serif;
    display: flex;
    align-items: center;
    justify-content: center;
    gap: 40px;
  }
  .card {
    position: relative;
    width: 520px;
    height: 297px;
    overflow: hidden;
    box-shadow: 0 10px 24px rgba(0,0,0,.45);
  }
  .card__art { position: absolute; inset: 0; width: 100%; height: 100%; }

  /* Front */
  .card--front { background: var(--paper); }
  .brand {
    position: absolute;
    font-weight: 700;
    letter-spacing: .5px;
    display: flex;
    align-items: center;
    gap: 10px;
  }
  .brand__dot { width: 12px; height: 12px; border-radius: 50%; background: currentColor; }
  .card--front .brand { color: var(--navy); font-size: 30px; left: 218px; top: 100px; }
  .holder { position: absolute; left: 300px; top: 212px; }
  .holder__name { color: var(--navy); font-weight: 700; font-size: 17px; letter-spacing: .8px; text-transform: uppercase; }
  .holder__role { color: var(--grey-text); font-size: 13px; margin-top: 2px; }
  .contact {
    position: absolute;
    left: 18px;
    top: 146px;
    list-style: none;
    color: var(--white);
    font-size: 12px;
    line-height: 17px;
  }
  .contact li { display: flex; align-items: center; gap: 6px; }
  .contact svg { width: 10px; height: 10px; fill: var(--white); flex: none; }
  .contact .contact__address { margin-top: 4px; display: block; }

  /* Back */
  .card--back { background: var(--navy-deep); }
  .card--back .brand { color: var(--white); font-size: 32px; left: 0; right: 0; top: 118px; justify-content: center; }
  .card--back .site {
    position: absolute; left: 0; right: 0; top: 192px;
    text-align: center; color: var(--white); font-size: 12px; letter-spacing: 1px;
  }
</style>
</head>
<body>

<section class="card card--front">
  <svg class="card__art" viewBox="0 0 520 297" aria-hidden="true">
    <path d="M70 0 C150 120 250 245 440 297 L400 297 C220 250 120 130 35 0 Z" fill="var(--silver)"/>
    <path d="M0 0 L35 0 C120 130 220 250 400 297 L0 297 Z" fill="var(--navy)"/>
  </svg>
  <ul class="contact">
    <li><svg viewBox="0 0 10 10"><path d="M2 0.5 L4 2.5 L3 3.5 Q4 6 6.5 7 L7.5 6 L9.5 8 L8 9.5 Q1 8 0.5 2 Z"/></svg>044-555 210 384</li>
    <li><svg viewBox="0 0 10 10"><path d="M0 2 H10 V8 H0 Z M0.8 2.6 L5 5.6 L9.2 2.6" stroke="var(--navy)" stroke-width="0.7"/></svg>info@meridianaxis.com</li>
    <li><svg viewBox="0 0 10 10"><circle cx="5" cy="5" r="4.5"/></svg>www.meridianaxis.com</li>
    <li class="contact__address">210, Harbour Street East<br>United Kingdom, EC2 4LP</li>
  </ul>
  <div class="brand"><span class="brand__name">Meridian Axis</span><span class="brand__dot"></span></div>
  <div class="holder">
    <p class="holder__name">Daniel Porter</p>
    <p class="holder__role">Managing Director</p>
  </div>
</section>

<section class="card card--back">
  <svg class="card__art" viewBox="0 0 520 297" aria-hidden="true">
    <path d="M170 0 C110 70 290 250 520 297 L520 0 Z" fill="var(--navy-light)"/>
  </svg>
  <div class="brand"><span class="brand__name">Meridian Axis</span><span class="brand__dot"></span></div>
  <p class="site">www.meridianaxis.com</p>
</section>

</body>
</html>
```